stationary deign for trucking company

im a trucking company looking for a professional set of stationary designs i deliver goods from point a to b
Updates

When submitting stationary designs I need envelope design, letterhead, cards, I’d badge etc

Industry/Entity Type

Trucking Company

Requirements
Must have
• must have letter head, business card, envelope, fax sheet, id badge, folder, thank you card, notebook, invoice sheet.
Nice to have
• nice to have them all custom made (letterhead,envelope, business card, I’d badge etc
Should not have
• must not have prepaid sign want i unique design for items

```html
<!DOCTYPE html>
<html lang="en">
<head>
<meta charset="utf-8">
<title>Halvorsen Stationery Set</title>
<link href="https://fonts.googleapis.com/css2?family=Montserrat:wght@400;500;600;700&family=Hind:wght@400;500&display=swap" rel="stylesheet">
<style>
  :root{
    --brand:#1557a8;
    --brand-dark:#0f4a93;
    --ink:#2a2a2a;
    --muted:#6a6a6a;
    --paper:#ffffff;
    --stage:#e3e4e2;
    --label:#27415f;
    --photo:#9aa3ab;
    --sig:#eceff3;
  }
  *{box-sizing:border-box;margin:0;padding:0}
  html,body{width:707px;height:1200px;overflow:hidden}
  body{background:var(--stage);font-family:"Montserrat",sans-serif;color:var(--ink);position:relative}
  .piece{position:absolute;background:var(--paper);box-shadow:0 1px 3px rgba(0,0,0,.18)}
  .label{position:absolute;font-family:"Hind",sans-serif;font-size:13px;color:var(--label);text-align:center}
  .brandbar{position:absolute;left:0;right:0;bottom:0;background:var(--brand)}
  .wordmark{position:absolute;font-weight:600;letter-spacing:.12em;color:var(--ink);white-space:nowrap}
  .wordmark small{display:block;font-weight:400;letter-spacing:.2em;color:var(--ink)}
  .blue{color:var(--brand)}
  .contact{position:absolute;display:flex;white-space:nowrap}
  .contact .addr{padding-right:5px;border-right:.6px solid var(--brand)}
  .contact .addr b{color:var(--brand);font-weight:700;display:block}
  .contact .lines{padding-left:5px}
  .contact .lines span{display:flex;align-items:center;gap:2px}
  .contact svg{fill:var(--brand)}

  /* business cards */
  .card-front{left:67px;top:66px;width:122px;height:68px}
  .card-front .wordmark{left:10px;top:27px;font-size:6.4px}
  .card-front .wordmark small{font-size:1.9px;margin-top:1px}
  .card-front .divider{position:absolute;left:73px;top:16px;width:.6px;height:36px;background:var(--muted)}
  .card-front .person{position:absolute;left:78px;top:18px;font-size:3px;line-height:4.4px;white-space:nowrap}
  .card-front .person b{color:var(--brand);font-weight:700;font-size:3.3px}
  .card-back{left:210px;top:66px;width:122px;height:68px;background:var(--brand)}
  .card-back .ghost{position:absolute;left:0;right:0;top:29px;text-align:center;font-weight:600;font-size:8px;letter-spacing:.12em;color:var(--brand-dark)}

  /* letterheads */
  .sheet{top:170px;width:250px;height:353px}
  .sheet-plain{left:72px}
  .sheet-word{left:372px;width:273px}
  .sheet .wordmark{left:15px;top:32px;font-size:9.5px}
  .sheet .wordmark small{font-size:2.7px;margin-top:1px}
  .sheet .contact{top:30px;font-size:3.6px;line-height:5.8px}
  .sheet-plain .contact{left:138px}
  .sheet-word .contact{left:150px}
  .letter{position:absolute;left:18px;right:18px;top:118px;font-size:4.4px;line-height:8.8px;color:#333}
  .letter .to b{color:var(--brand);font-weight:700;font-size:5px}
  .letter .to{line-height:8.8px}
  .letter .date{position:absolute;right:0;top:0;font-weight:500}
  .letter p{margin-top:14px;text-align:justify}
  .letter p + p{margin-top:9px}
  .letter .close{margin-top:8px;font-size:3.4px;line-height:5px}
  .signature{display:block;width:38px;height:13px;background:var(--sig);margin:2px 0}

  /* envelopes */
  .env{top:578px;height:142px}
  .env-front{left:20px;width:324px}
  .env-front .wordmark{left:20px;top:22px;font-size:10px}
  .env-front .wordmark small{font-size:2.8px;margin-top:1px}
  .env-front .sender{position:absolute;left:19px;top:96px;padding-left:6px;border-left:1px solid var(--brand);font-size:5px;line-height:9px}
  .env-front .sender b{color:var(--brand);font-weight:700}
  .env-back{left:364px;width:320px}
  .env-back svg.flap{position:absolute;left:0;top:0}
  .env-back .flapname{position:absolute;left:0;right:0;top:19px;text-align:center;color:#fff;font-weight:600;font-size:11px;letter-spacing:.14em}

  /* id badge */
  .badge{left:280px;top:920px;width:140px;height:212px;border-radius:6px;border:4px solid #f1f2f3;overflow:hidden}
  .badge .wordmark{left:0;right:0;top:16px;text-align:center;font-size:9px}
  .badge .wordmark small{font-size:2.6px;margin-top:1px}
  .badge .photo{position:absolute;left:51px;top:47px;width:38px;height:38px;background:var(--photo);outline:1px solid var(--brand);outline-offset:2px}
  .badge .name{position:absolute;left:0;right:0;top:98px;text-align:center;font-size:6px;font-weight:700;color:var(--brand)}
  .badge .role{position:absolute;left:0;right:0;top:106px;text-align:center;font-size:4px;color:var(--muted)}
  .badge dl{position:absolute;left:24px;top:128px;display:grid;grid-template-columns:18px 6px auto;font-size:4.4px;line-height:7px}
  .badge dt{color:var(--brand);font-weight:600}
  .badge .brandbar{height:3px;bottom:6px;left:8px;right:8px}
</style>
</head>
<body>

  <!-- Business card -->
  <section class="piece card-front">
    <div class="wordmark">HALVORSEN<small>TRANSPORTATION • LOGISTICS</small></div>
    <div class="divider"></div>
    <div class="person">
      <b>DANIEL OKAFOR</b><br>
      Senior Consultant<br>
      418 W 12th St. Ste<br>
      210 Riverton, VA 23510<br>
      (555) 014-2290<br>
      info@halvorsenfreight.com<br>
      www.halvorsenfreight.com
    </div>
    <div class="brandbar" style="height:2px"></div>
  </section>
  <section class="piece card-back"><div class="ghost">HALVORSEN</div></section>
  <div class="label" style="left:67px;width:112px;top:141px">Business card</div>

  <!-- Letterhead -->
  <section class="piece sheet sheet-plain">
    <div class="wordmark">HALVORSEN<small>TRANSPORTATION • LOGISTICS</small></div>
    <div class="contact">
      <div class="addr"><b>HALVORSEN</b>418 W 12th St. Ste<br>210 Riverton, VA 23510</div>
      <div class="lines">
        <span><svg width="4" height="4" viewBox="0 0 10 10"><path d="M2 0h2l1 3-1.5 1a6 6 0 0 0 2.5 2.5L7 5l3 1v2a2 2 0 0 1-2 2A8 8 0 0 1 0 2a2 2 0 0 1 2-2z"/></svg>(555) 014-2290</span>
        <span><svg width="4" height="4" viewBox="0 0 10 10"><path d="M0 2h10v6H0zM1 3l4 3 4-3" fill="none" stroke="#1557a8" stroke-width="1"/></svg>info@halvorsenfreight.com</span>
        <span><svg width="4" height="4" viewBox="0 0 10 10"><circle cx="5" cy="5" r="5"/></svg>www.halvorsenfreight.com</span>
      </div>
    </div>
    <div class="brandbar" style="height:3px"></div>
  </section>
  <div class="label" style="left:72px;width:250px;top:544px">Letterhead</div>

  <!-- Word document letterhead -->
  <section class="piece sheet sheet-word">
    <div class="wordmark">HALVORSEN<small>TRANSPORTATION • LOGISTICS</small></div>
    <div class="contact">
      <div class="addr"><b>HALVORSEN</b>418 W 12th St. Ste<br>210 Riverton, VA 23510</div>
      <div class="lines">
        <span><svg width="4" height="4" viewBox="0 0 10 10"><path d="M2 0h2l1 3-1.5 1a6 6 0 0 0 2.5 2.5L7 5l3 1v2a2 2 0 0 1-2 2A8 8 0 0 1 0 2a2 2 0 0 1 2-2z"/></svg>(555) 014-2290</span>
        <span><svg width="4" height="4" viewBox="0 0 10 10"><path d="M0 2h10v6H0zM1 3l4 3 4-3" fill="none" stroke="#1557a8" stroke-width="1"/></svg>info@halvorsenfreight.com</span>
        <span><svg width="4" height="4" viewBox="0 0 10 10"><circle cx="5" cy="5" r="5"/></svg>www.halvorsenfreight.com</span>
      </div>
    </div>
    <div class="letter">
      <div class="to"><b>Daniel Okafor</b><br>Manager<br>1234 Street Name<br>Greenfield, NC</div>
      <div class="date">Date: 31/01/2019</div>
      <p>Lorem ipsum dolor sit amet, consectetuer adipiscing elit, sed diam nonummy nibh euismod tincidunt ut laoreet dolore magna aliquam erat volutpat. Ut wisi enim ad minim veniam, quis nostrud exerci tation ullamcorper suscipit lobortis nisl ut aliquip ex ea commodo consequat. Lorem ipsum dolor sit amet, cons ectetuer adipiscing elit, sed diam nonummy nibh euismod tincidunt ut laoreet dolore magna aliquam erat volutpat. Ut wisi enim ad minim veniam, quis nostrud exerci tation ullamcorper suscipit lobortis nisl ut aliquip ex ea commodo consequat. Lorem ipsum dolor sit amet, consectetuer adipiscing elit, sed diam nonummy nibh euismod tincidunt ut laoreet dolore magna aliquam erat volutpat. Ut wisi enim ad minim veniam.</p>
      <p>consequat. Duis autem vel eum iriure dolor in hendrerit in vulputate velit esse molestie consequat, vel illum dolore eu feugiat nulla facilisis at vero eros et accumsan.</p>
      <div class="close">sincerely<span class="signature" role="img" aria-label="Handwritten signature"></span>Daniel Okafor</div>
    </div>
    <div class="brandbar" style="height:3px"></div>
  </section>
  <div class="label" style="left:372px;width:273px;top:544px">Word Document Letterhead</div>

  <!-- Envelope -->
  <section class="piece env env-front">
    <div class="wordmark">HALVORSEN<small>TRANSPORTATION • LOGISTICS</small></div>
    <div class="sender"><b>HALVORSEN</b><br>418 W 12th St. Ste<br>210 Riverton, VA 23510</div>
    <div class="brandbar" style="height:3px"></div>
  </section>
  <div class="label" style="left:20px;width:324px;top:747px">Envelope Front</div>

  <section class="piece env env-back">
    <svg class="flap" width="320" height="54" viewBox="0 0 320 54"><polygon points="0,0 320,0 316,52 4,52" fill="#1557a8"/></svg>
    <div class="flapname">HALVORSEN</div>
  </section>
  <div class="label" style="left:364px;width:320px;top:747px">Envelope Back</div>

  <!-- ID badge -->
  <section class="piece badge">
    <div class="wordmark">HALVORSEN<small>TRANSPORTATION • LOGISTICS</small></div>
    <div class="photo" role="img" aria-label="Staff portrait photo"></div>
    <div class="name">DANIEL OKAFOR</div>
    <div class="role">Senior Consultant</div>
    <dl>
      <dt>Id No</dt><dd>:</dd><dd>01254</dd>
      <dt>Email</dt><dd>:</dd><dd>info@halvorsenfreight.com</dd>
      <dt>Phone</dt><dd>:</dd><dd>(555) 014-2290</dd>
      <dt>Blood</dt><dd>:</dd><dd>(A+)</dd>
    </dl>
    <div class="brandbar"></div>
  </section>
  <div class="label" style="left:280px;width:140px;top:1167px">Id card</div>

</body>
</html>
```